Modern Verdell Tree Care Website

I need a website for a full service Tree Care company. The company provides tree pruning, tree removal, tree preservation, emergency services, stump grinding, and emergency tree services.

Target Market(s)

Customers that need tree services

Industry/Entity Type

Landscaping, Tree Services

Coding

Coded - Design and coding required

Number of Pages Required

5+ page

Font styles to use
Sans Serif

Requirements
Must have
• Good clean design that showcases the services the company provides.
Nice to have
• Services page; contact form, blog, home page, about page

```html
<!DOCTYPE html>
<html lang="en">
<head>
<meta charset="utf-8">
<title>Verdell Tree Care</title>
<link href="https://fonts.googleapis.com/css2?family=Montserrat:wght@600;700;800;900&family=Poppins:wght@400;500;600&display=swap" rel="stylesheet">
<style>
:root{
  --green:#7bb32e;
  --green-dark:#5f9a1d;
  --orange:#f5a52a;
  --orange-soft:#f7b23c;
  --slate:#55616b;
  --ink:#3d4650;
  --muted:#6b7177;
  --line:#d9d9d9;
  --field:#efefef;
  --footer:#0e1a10;
  --white:#fff;
}
*{box-sizing:border-box;margin:0;padding:0}
html,body{width:1200px;height:5199px;overflow:hidden}
body{font-family:"Poppins",sans-serif;color:var(--ink);background:var(--white);position:relative}
.abs{position:absolute}
h1,h2,h3,.heading{font-family:"Montserrat",sans-serif}
a{color:inherit;text-decoration:none}

/* buttons */
.btn{position:absolute;display:flex;align-items:center;gap:8px;height:50px;padding:0 36px 0 28px;background:var(--green);color:#fff;font:700 13px "Montserrat",sans-serif;text-transform:uppercase;letter-spacing:.2px}
.btn::after{content:"";position:absolute;right:-14px;top:0;width:26px;height:50px;background:var(--orange);clip-path:polygon(0 0,100% 0,100% 100%)}
.btn.orange{background:var(--orange)}
.btn.orange::after{background:#f7c56e}
.arrow-dot{width:14px;height:14px;border-radius:50%;background:#fff;display:inline-flex;align-items:center;justify-content:center}
.arrow-dot svg{width:8px;height:8px}

/* header */
.topbar{left:632px;top:0;width:568px;height:46px;background:var(--green);clip-path:polygon(4% 0,100% 0,100% 100%,0 100%);color:#fff;font-size:14px;display:flex;align-items:center;gap:22px;padding-left:48px}
.topbar .ph{display:flex;align-items:center;gap:12px}
.ring{width:32px;height:32px;border-radius:50%;border:2px solid #fff;display:flex;align-items:center;justify-content:center}
.brand{left:118px;top:30px;display:flex;align-items:center;gap:12px}
.brand-mark{width:46px;height:46px;background:var(--green)}
.brand-name{font:800 32px/1 "Montserrat",sans-serif;color:var(--slate);letter-spacing:.5px}
.brand-sub{font:600 16px/1 "Montserrat",sans-serif;color:var(--slate);letter-spacing:5px;margin-top:6px}
.nav{left:450px;top:74px;display:flex;gap:36px;font:500 14px "Poppins",sans-serif;color:var(--ink)}
.nav a.active{position:relative}
.nav a.active::after{content:"";position:absolute;left:8px;right:8px;top:28px;height:3px;background:var(--orange)}
.socials{display:flex;gap:12px}
.social{width:44px;height:44px;border-radius:50%;border:1.5px solid var(--slate)}
.header-social{left:920px;top:62px}

/* hero */
.hero{left:0;top:118px;width:1200px;height:636px;background:linear-gradient(100deg,#1c2a12 0%,#324a1a 40%,#5a6a2a 62%,#2d3a18 100%)}
.hero-photo{position:absolute;inset:0;background:radial-gradient(circle at 70% 40%,rgba(220,170,30,.35),transparent 40%),radial-gradient(circle at 55% 75%,rgba(230,90,30,.35),transparent 30%)}
.hero-tag{left:120px;top:292px;height:34px;padding:0 38px 0 36px;background:var(--green);color:#fff;font:800 19px/34px "Montserrat",sans-serif;clip-path:polygon(4% 0,100% 0,96% 100%,0 100%)}
.hero-title{left:118px;top:334px;color:#fff;font:900 61px/66px "Montserrat",sans-serif}
.hero-sub{left:120px;top:480px;color:#fff;font:600 15px "Montserrat",sans-serif}
.hero-nav{top:382px;width:40px;height:60px}
.dots{left:568px;top:712px;display:flex;gap:10px}
.dots i{width:8px;height:8px;border-radius:50%;background:#fff;opacity:.8}
.dots i.on{background:var(--green);opacity:1}

/* section headings */
.sec-title{left:0;width:1200px;text-align:center;font:800 44px/1 "Montserrat",sans-serif;color:var(--slate)}
.sec-sub{left:0;width:1200px;text-align:center;font:600 15px/1 "Montserrat",sans-serif;color:var(--green);letter-spacing:8px}
.sec-line{left:572px;width:56px;height:3px;background:var(--orange)}

/* services */
.card{position:absolute;width:308px;height:366px;border:2px solid var(--line);background:#fff;text-align:center}
.card .ph-img{margin:10px;height:172px;width:284px}
.card h3{font:700 17px "Montserrat",sans-serif;color:var(--ink);margin-top:26px}
.card .bar{width:48px;height:3px;background:var(--orange);margin:8px auto 16px}
.card p{font-size:15px;line-height:28px;color:var(--muted)}
.card .more{display:inline-flex;align-items:center;gap:8px;margin-top:14px;font:700 13px "Montserrat",sans-serif;color:var(--green)}
.card .more .arrow-dot{background:var(--green)}

/* about */
.about{left:0;top:1912px;width:1200px;height:624px;background:var(--green)}
.about-photo{position:absolute;left:0;top:0;width:640px;height:624px;clip-path:polygon(0 0,100% 0,64% 100%,0 100%);background:linear-gradient(135deg,#2e3f1e,#6a7a3a 50%,#d98a1f 75%,#3a4a24)}
.about-title{left:630px;top:2015px;color:#fff;font:900 44px/1 "Montserrat",sans-serif}
.about-sub{left:632px;top:2070px;color:#fff;font:600 15px "Montserrat",sans-serif;letter-spacing:7px}
.about-text{left:630px;top:2124px;width:450px;color:#fff;font-size:15px;line-height:27px}

/* why */
.why-label{font:700 13.5px/25px "Montserrat",sans-serif;color:var(--ink)}
.why-label.l{text-align:right}
.icon-circle{position:absolute;width:120px;height:120px;border-radius:50%;background:#fff;border:5px solid;display:flex;align-items:center;justify-content:center;box-shadow:0 8px 10px -6px rgba(0,0,0,.2)}
.icon-circle.o{border-color:#d3b483}
.icon-circle.g{border-color:var(--green)}
.core{left:475px;top:2852px;width:250px;height:250px;border-radius:50%;border:6px solid #cfc7c0;display:flex;align-items:center;justify-content:center}
.core-inner{width:210px;height:210px;border-radius:50%;background:#fff;display:flex;align-items:center;justify-content:center;font:800 26px "Montserrat",sans-serif;color:var(--green)}

/* contact */
.contact-band{left:0;top:3272px;width:1200px;height:448px;background:linear-gradient(100deg,#f2a52e,#f6b448 50%,#efa223)}
.contact-title{color:#fff}
.contact-card{left:120px;top:3500px;width:960px;height:426px;background:#fff;box-shadow:0 6px 20px rgba(0,0,0,.08)}
.field{position:absolute;background:var(--field);color:#8a8f94;font-size:13.5px;padding:14px 20px}
.contact-phone{display:flex;align-items:center;gap:12px;color:#8a8f94;font-size:14px}
.ring.o{border-color:var(--orange)}

/* news */
.post{position:absolute;width:312px}
.post .ph-img{height:237px}
.post h3{font:700 17px/28px "Montserrat",sans-serif;color:var(--slate);margin-top:22px}
.post .meta{display:flex;gap:18px;margin-top:22px;font-size:13px;color:var(--muted)}
.post .meta span{display:flex;align-items:center;gap:6px}

/* footer */
.footer{left:0;top:4690px;width:1200px;height:509px;background:var(--footer);color:#fff}
.foot-h{font:800 17px "Montserrat",sans-serif}
.foot-links a{display:block;font-size:15px;line-height:41px}
.foot-contact{display:flex;gap:18px;align-items:flex-start;margin-bottom:20px;font-size:15px;line-height:25px}
.pin{width:44px;height:44px;border-radius:50%;background:var(--orange);flex:none;display:flex;align-items:center;justify-content:center}
.footer .social{border-color:#6d746d}
</style>
</head>
<body>

<!-- Header -->
<header>
  <div class="abs topbar">
    <span class="ph"><span class="ring"><svg width="14" height="14" viewBox="0 0 24 24"><path d="M6.6 10.8a15 15 0 0 0 6.6 6.6l2.2-2.2c.3-.3.7-.4 1-.2 1.1.4 2.3.6 3.6.6.6 0 1 .4 1 1V20c0 .6-.4 1-1 1A17 17 0 0 1 3 4c0-.6.4-1 1-1h3.5c.6 0 1 .4 1 1 0 1.3.2 2.5.6 3.6.1.3 0 .7-.2 1z" fill="#fff"/></svg></span>(555) 204-7316</span>
    <span style="opacity:.8">|</span>
    <span class="ph"><span class="ring"><svg width="14" height="14" viewBox="0 0 24 24"><path d="M6.6 10.8a15 15 0 0 0 6.6 6.6l2.2-2.2c.3-.3.7-.4 1-.2 1.1.4 2.3.6 3.6.6.6 0 1 .4 1 1V20c0 .6-.4 1-1 1A17 17 0 0 1 3 4c0-.6.4-1 1-1h3.5c.6 0 1 .4 1 1 0 1.3.2 2.5.6 3.6.1.3 0 .7-.2 1z" fill="#fff"/></svg></span>(555) 318-4620</span>
  </div>
  <div class="abs brand">
    <div class="brand-mark"></div>
    <div><div class="brand-name">VERDELL</div><div class="brand-sub">TREE CARE</div></div>
  </div>
  <nav class="abs nav">
    <a class="active">HOME</a><a>ABOUT</a><a>SERVICES</a><a>BLOG</a><a>CONTACT</a>
  </nav>
  <div class="abs socials header-social">
    <span class="social" aria-label="Social profile"></span><span class="social" aria-label="Social profile"></span><span class="social" aria-label="Social profile"></span>
  </div>
</header>

<!-- Hero -->
<section class="abs hero" role="img" aria-label="Arborist in safety gear cutting a log with a chainsaw in the forest">
  <div class="hero-photo"></div>
</section>
<div class="abs hero-tag">CALL VERDELL FOR</div>
<h1 class="abs hero-title">ALL YOUR TREE<br>CARE NEEDS.</h1>
<div class="abs hero-sub">SERVING BROOKHAVEN AND SURROUNDING AREAS</div>
<a class="btn orange" style="left:120px;top:530px">Get Free Estimate <span class="arrow-dot"><svg viewBox="0 0 10 10"><path d="M3 2l3 3-3 3" stroke="var(--orange)" stroke-width="2" fill="none"/></svg></span></a>
<svg class="abs hero-nav" style="left:44px" viewBox="0 0 40 60"><path d="M30 2L4 30l26 28" stroke="#fff" stroke-width="2.5" fill="none"/></svg>
<svg class="abs hero-nav" style="left:1116px" viewBox="0 0 40 60"><path d="M10 2l26 28-26 28" stroke="#fff" stroke-width="2.5" fill="none"/></svg>
<div class="abs dots"><i></i><i class="on"></i><i></i></div>

<!-- Services -->
<h2 class="abs sec-title" style="top:845px">OUR SERVICES</h2>
<div class="abs sec-sub" style="top:898px">WHAT WE DO</div>
<div class="abs sec-line" style="top:920px"></div>

<article class="card" style="left:120px;top:978px">
  <div class="ph-img" role="img" aria-label="Worker trimming a hedge" style="background:linear-gradient(135deg,#7a3a2a,#3f6a2a 55%,#e3e0da)"></div>
  <h3>TREE TRIMMING</h3><div class="bar"></div>
  <p>Incididunt ut labore et dolore<br>maga aliqua ut enim ado.</p>
  <a class="more">VIEW MORE <span class="arrow-dot"><svg viewBox="0 0 10 10"><path d="M3 2l3 3-3 3" stroke="#fff" stroke-width="2" fill="none"/></svg></span></a>
</article>
<article class="card" style="left:445px;top:978px">
  <div class="ph-img" role="img" aria-label="Arborist removing a cut tree trunk" style="background:linear-gradient(160deg,#9cc3df,#7a9a3a 50%,#c2a376)"></div>
  <h3>TREE REMOVAL</h3><div class="bar"></div>
  <p>Incididunt ut labore et dolore<br>maga aliqua ut enim ado.</p>
  <a class="more">VIEW MORE <span class="arrow-dot"><svg viewBox="0 0 10 10"><path d="M3 2l3 3-3 3" stroke="#fff" stroke-width="2" fill="none"/></svg></span></a>
</article>
<article class="card" style="left:771px;top:978px">
  <div class="ph-img" role="img" aria-label="Red machine clearing fallen trees" style="background:linear-gradient(135deg,#4a5a2a,#b8382a 50%,#6a5a3a)"></div>
  <h3>TREE CLEARING</h3><div class="bar"></div>
  <p>Incididunt ut labore et dolore<br>maga aliqua ut enim ado.</p>
  <a class="more">VIEW MORE <span class="arrow-dot"><svg viewBox="0 0 10 10"><path d="M3 2l3 3-3 3" stroke="#fff" stroke-width="2" fill="none"/></svg></span></a>
</article>
<article class="card" style="left:120px;top:1362px">
  <div class="ph-img" role="img" aria-label="Chainsaw cutting through a log" style="background:linear-gradient(135deg,#2f4a1e,#c9a276 55%,#e0802a)"></div>
  <h3>TREE PRUNING</h3><div class="bar"></div>
  <p>Incididunt ut labore et dolore<br>maga aliqua ut enim ado.</p>
  <a class="more">VIEW MORE <span class="arrow-dot"><svg viewBox="0 0 10 10"><path d="M3 2l3 3-3 3" stroke="#fff" stroke-width="2" fill="none"/></svg></span></a>
</article>
<article class="card" style="left:445px;top:1362px">
  <div class="ph-img" role="img" aria-label="Stump grinder at work" style="background:linear-gradient(135deg,#d8cfb8,#3b5a2e 50%,#6a5030)"></div>
  <h3>STUMP GRINDING</h3><div class="bar"></div>
  <p>Incididunt ut labore et dolore<br>maga aliqua ut enim ado.</p>
  <a class="more">VIEW MORE <span class="arrow-dot"><svg viewBox="0 0 10 10"><path d="M3 2l3 3-3 3" stroke="#fff" stroke-width="2" fill="none"/></svg></span></a>
</article>
<article class="card" style="left:771px;top:1362px">
  <div class="ph-img" role="img" aria-label="Old oak with sprawling branches" style="background:linear-gradient(135deg,#5a6a3a,#3a3a2a 50%,#8a9a5a)"></div>
  <h3>TREE PRESERVATION</h3><div class="bar"></div>
  <p>Incididunt ut labore et dolore<br>maga aliqua ut enim ado.</p>
  <a class="more">VIEW MORE <span class="arrow-dot"><svg viewBox="0 0 10 10"><path d="M3 2l3 3-3 3" stroke="#fff" stroke-width="2" fill="none"/></svg></span></a>
</article>
<a class="btn" style="left:514px;top:1765px">View More <span class="arrow-dot"><svg viewBox="0 0 10 10"><path d="M3 2l3 3-3 3" stroke="var(--green)" stroke-width="2" fill="none"/></svg></span></a>

<!-- About -->
<section class="abs about">
  <div class="about-photo" role="img" aria-label="Arborist in orange gear and helmet looking up at a tree trunk"></div>
</section>
<h2 class="abs about-title">ABOUT VERDELL</h2>
<div class="abs about-sub">TREE CARE</div>
<p class="abs about-text">At Verdell Tree Care, we are more than just a tree service company, we are stewards of our beautiful trees. With a passion deeply rooted in arboriculture, we embark on a mission to promote the health, beauty, and safety of your trees and landscapes. Whether it's expert tree trimming to enhance aesthetics, meticulous tree removal to mitigate hazards, or comprehensive tree health assessments to ensure safety...</p>
<a class="btn orange" style="left:630px;top:2372px">View More <span class="arrow-dot"><svg viewBox="0 0 10 10"><path d="M3 2l3 3-3 3" stroke="var(--orange)" stroke-width="2" fill="none"/></svg></span></a>

<!-- Why choose us -->
<h2 class="abs sec-title" style="top:2628px">WHY CHOOSE US</h2>
<div class="abs sec-sub" style="top:2680px">WHAT OUR DIFFERENT</div>
<div class="abs sec-line" style="top:2702px"></div>

<svg class="abs" style="left:0;top:2780px" width="1200" height="390" viewBox="0 0 1200 390">
  <g fill="none" stroke-width="4" stroke-linecap="round">
    <path d="M440 50c30 0 40 12 50 30" stroke="#d3b483"/>
    <path d="M440 170c25 10 35 10 50 0" stroke="var(--green)"/>
    <path d="M385 188c30 12 60 12 90 0" stroke="var(--green)"/>
    <path d="M440 330c30 0 40-12 50-30" stroke="var(--orange)"/>
    <path d="M760 50c-30 0-40 12-50 30" stroke="#d3b483"/>
    <path d="M760 170c-25 10-35 10-50 0" stroke="var(--green)"/>
    <path d="M815 188c-30 12-60 12-90 0" stroke="var(--green)"/>
    <path d="M760 330c-30 0-40-12-50-30" stroke="var(--orange)"/>
  </g>
</svg>
<div class="abs core"><div class="core-inner">VERDELL</div></div>

<div class="icon-circle o" style="left:314px;top:2765px"><svg width="48" height="48" viewBox="0 0 48 48"><rect x="8" y="6" width="24" height="32" rx="3" fill="none" stroke="#c9a06a" stroke-width="3"/><path d="M14 16h12M14 23h8" stroke="#c9a06a" stroke-width="3"/><path d="M30 26l10 4v6c0 5-4 8-10 10-6-2-10-5-10-10v-6z" fill="#c9a06a"/><path d="M26 36l3 3 6-6" stroke="#fff" stroke-width="2.5" fill="none"/></svg></div>
<div class="icon-circle g" style="left:254px;top:2908px"><svg width="48" height="48" viewBox="0 0 48 48"><circle cx="24" cy="15" r="7" fill="var(--green)"/><path d="M10 42c0-9 6-15 14-15s14 6 14 15z" fill="var(--green)"/><path d="M16 10h16" stroke="var(--green)" stroke-width="4"/></svg></div>
<div class="icon-circle o" style="left:314px;top:3052px"><svg width="48" height="48" viewBox="0 0 48 48"><rect x="14" y="6" width="24" height="34" rx="3" fill="none" stroke="var(--orange)" stroke-width="3"/><path d="M20 16h12M20 23h12M20 30h8" stroke="var(--orange)" stroke-width="3"/><circle cx="12" cy="30" r="7" fill="var(--orange)"/></svg></div>
<div class="icon-circle o" style="left:766px;top:2765px"><svg width="48" height="48" viewBox="0 0 48 48"><path d="M8 34V18l10-8 10 8v16z" fill="none" stroke="#c9a06a" stroke-width="3"/><path d="M22 26h20l-4 8H22z" fill="#c9a06a"/></svg></div>
<div class="icon-circle g" style="left:826px;top:2908px"><svg width="48" height="48" viewBox="0 0 48 48"><rect x="8" y="8" width="24" height="30" rx="3" fill="var(--green)"/><path d="M13 16h14M13 22h10" stroke="#fff" stroke-width="3"/><circle cx="34" cy="32" r="9" fill="var(--green)" stroke="#fff" stroke-width="2"/><path d="M30 32l3 3 5-5" stroke="#fff" stroke-width="2.5" fill="none"/></svg></div>
<div class="icon-circle o" style="left:766px;top:3052px"><svg width="48" height="48" viewBox="0 0 48 48"><circle cx="20" cy="20" r="7" fill="var(--orange)"/><path d="M6 42c0-9 6-14 14-14s14 5 14 14z" fill="var(--orange)"/><path d="M34 6l8 3v6c0 4-3 7-8 8-5-1-8-4-8-8V9z" fill="var(--orange)"/></svg></div>

<div class="abs why-label l" style="left:120px;top:2800px;width:176px">LICENSED AND<br>INSURED</div>
<div class="abs why-label l" style="left:90px;top:2943px;width:146px">HIGHLY<br>PRO WORK</div>
<div class="abs why-label l" style="left:110px;top:3087px;width:186px">LICENSED<br>ARBORIST ON STAFF</div>
<div class="abs why-label" style="left:902px;top:2800px">LOCALLY OWNED<br>&amp; OPERATED</div>
<div class="abs why-label" style="left:962px;top:2943px">FREE<br>ESTIMATE</div>
<div class="abs why-label" style="left:902px;top:3087px">SAFETY IS OUR NO.1<br>PRIORITY</div>

<!-- Contact -->
<section class="abs contact-band" role="img" aria-label="Faded chainsaw work backdrop in orange tone"></section>
<h2 class="abs sec-title contact-title" style="top:3365px">CONTACT US</h2>
<div class="abs sec-sub" style="top:3418px;color:#fff">GET IN TOUCH</div>
<div class="abs sec-line" style="top:3440px;background:#fff"></div>

<section class="abs contact-card">
  <div class="abs" role="img" aria-label="Chainsaw cutting a fallen log" style="left:28px;top:28px;width:304px;height:370px;background:linear-gradient(150deg,#8a6a4a,#e0702a 35%,#b09070 60%,#4a3a2a)"></div>
  <div class="field" style="left:363px;top:28px;width:277px;height:52px">NAME</div>
  <div class="field" style="left:654px;top:28px;width:277px;height:52px">EMAIL</div>
  <div class="field" style="left:363px;top:97px;width:277px;height:52px">PHONE</div>
  <div class="field" style="left:654px;top:97px;width:277px;height:52px">SUBJECT</div>
  <div class="field" style="left:363px;top:165px;width:568px;height:163px">LEAVE A MESSAGE</div>
  <a class="btn" style="left:363px;top:350px;width:160px">Submit <span class="arrow-dot"><svg viewBox="0 0 10 10"><path d="M3 2l3 3-3 3" stroke="var(--green)" stroke-width="2" fill="none"/></svg></span></a>
  <div class="abs contact-phone" style="left:558px;top:358px"><span class="ring o"><svg width="14" height="14" viewBox="0 0 24 24"><path d="M6.6 10.8a15 15 0 0 0 6.6 6.6l2.2-2.2c.3-.3.7-.4 1-.2 1.1.4 2.3.6 3.6.6.6 0 1 .4 1 1V20c0 .6-.4 1-1 1A17 17 0 0 1 3 4c0-.6.4-1 1-1h3.5c.6 0 1 .4 1 1 0 1.3.2 2.5.6 3.6.1.3 0 .7-.2 1z" fill="var(--orange)"/></svg></span>(555) 204-7316</div>
  <div class="abs contact-phone" style="left:755px;top:358px"><span class="ring o"><svg width="14" height="14" viewBox="0 0 24 24"><path d="M6.6 10.8a15 15 0 0 0 6.6 6.6l2.2-2.2c.3-.3.7-.4 1-.2 1.1.4 2.3.6 3.6.6.6 0 1 .4 1 1V20c0 .6-.4 1-1 1A17 17 0 0 1 3 4c0-.6.4-1 1-1h3.5c.6 0 1 .4 1 1 0 1.3.2 2.5.6 3.6.1.3 0 .7-.2 1z" fill="var(--orange)"/></svg></span>(555) 318-4620</div>
</section>

<!-- News -->
<h2 class="abs sec-title" style="top:4020px">LATEST NEWS</h2>
<div class="abs sec-sub" style="top:4073px">READ OUR BLOG</div>
<div class="abs sec-line" style="top:4095px"></div>

<article class="post" style="left:120px;top:4155px">
  <div class="ph-img" role="img" aria-label="Worker cutting branches with a chainsaw" style="background:linear-gradient(135deg,#6a6a5a,#c9582a 55%,#4a4a3a)"></div>
  <h3>LOREM IPSUM DOLOR SIT AMET CONSECTETUR ADI</h3>
  <div class="meta"><span><svg width="12" height="12" viewBox="0 0 12 12"><circle cx="6" cy="4" r="3" fill="var(--orange)"/><path d="M1 12c0-3 2-5 5-5s5 2 5 5z" fill="var(--orange)"/></svg>Admin,</span><span><svg width="12" height="12" viewBox="0 0 12 12"><rect x="1" y="2" width="10" height="9" fill="var(--green)"/></svg>14 JUN 2024</span></div>
  <a class="btn" style="left:0;top:395px">View More <span class="arrow-dot"><svg viewBox="0 0 10 10"><path d="M3 2l3 3-3 3" stroke="var(--green)" stroke-width="2" fill="none"/></svg></span></a>
</article>
<article class="post" style="left:443px;top:4155px">
  <div class="ph-img" role="img" aria-label="Gloved hand pruning shrubs with shears" style="background:linear-gradient(135deg,#2f5a1e,#7ab040 50%,#d8d4c8)"></div>
  <h3>LOREM IPSUM DOLOR SIT AMET CONSECTETUR ADI</h3>
  <div class="meta"><span><svg width="12" height="12" viewBox="0 0 12 12"><circle cx="6" cy="4" r="3" fill="var(--orange)"/><path d="M1 12c0-3 2-5 5-5s5 2 5 5z" fill="var(--orange)"/></svg>Admin,</span><span><svg width="12" height="12" viewBox="0 0 12 12"><rect x="1" y="2" width="10" height="9" fill="var(--green)"/></svg>14 JUN 2024</span></div>
  <a class="btn" style="left:0;top:395px">View More <span class="arrow-dot"><svg viewBox="0 0 10 10"><path d="M3 2l3 3-3 3" stroke="var(--green)" stroke-width="2" fill="none"/></svg></span></a>
</article>
<article class="post" style="left:766px;top:4155px">
  <div class="ph-img" role="img" aria-label="Chainsaw slicing a log" style="background:linear-gradient(135deg,#3a6ab0,#e07a2a 45%,#c9a060 75%,#5a4a2a)"></div>
  <h3>LOREM IPSUM DOLOR SIT AMET CONSECTETUR ADI</h3>
  <div class="meta"><span><svg width="12" height="12" viewBox="0 0 12 12"><circle cx="6" cy="4" r="3" fill="var(--orange)"/><path d="M1 12c0-3 2-5 5-5s5 2 5 5z" fill="var(--orange)"/></svg>Admin,</span><span><svg width="12" height="12" viewBox="0 0 12 12"><rect x="1" y="2" width="10" height="9" fill="var(--green)"/></svg>14 JUN 2024</span></div>
  <a class="btn" style="left:0;top:395px">View More <span class="arrow-dot"><svg viewBox="0 0 10 10"><path d="M3 2l3 3-3 3" stroke="var(--green)" stroke-width="2" fill="none"/></svg></span></a>
</article>

<!-- Footer -->
<footer class="abs footer">
  <div class="abs" style="left:118px;top:95px;display:flex;align-items:center;gap:12px">
    <div class="brand-mark"></div>
    <div><div class="brand-name" style="color:#fff">VERDELL</div><div class="brand-sub" style="color:#fff">TREE CARE</div></div>
  </div>
  <p class="abs" style="left:120px;top:178px;width:310px;font-size:15px;line-height:27px">At Verdell Tree Care, we are more than just a tree service company, we are stewards of our beautiful trees.</p>
  <div class="abs socials" style="left:120px;top:278px">
    <span class="social" aria-label="Social profile"></span><span class="social" aria-label="Social profile"></span><span class="social" aria-label="Social profile"></span>
  </div>
  <div class="abs foot-h" style="left:555px;top:100px">QUICK LINKS</div>
  <nav class="abs foot-links" style="left:555px;top:135px"><a>Home</a><a>About</a><a>Services</a><a>Blog</a><a>Contact</a></nav>
  <div class="abs foot-h" style="left:810px;top:100px">CONTACT INFORMATION</div>
  <div class="abs" style="left:810px;top:145px;width:280px">
    <div class="foot-contact"><span class="pin"><svg width="16" height="18" viewBox="0 0 16 20"><path d="M8 0a7 7 0 0 0-7 7c0 5 7 13 7 13s7-8 7-13a7 7 0 0 0-7-7z" fill="#fff"/><circle cx="8" cy="7" r="2.5" fill="var(--orange)"/></svg></span><span>Inventore veritatis et mani quasi architecto</span></div>
    <div class="foot-contact"><span class="pin"><svg width="16" height="16" viewBox="0 0 24 24"><path d="M6.6 10.8a15 15 0 0 0 6.6 6.6l2.2-2.2c.3-.3.7-.4 1-.2 1.1.4 2.3.6 3.6.6.6 0 1 .4 1 1V20c0 .6-.4 1-1 1A17 17 0 0 1 3 4c0-.6.4-1 1-1h3.5c.6 0 1 .4 1 1 0 1.3.2 2.5.6 3.6.1.3 0 .7-.2 1z" fill="#fff"/></svg></span><span>Call us:<br>(555) 204-7316</span></div>
    <div class="foot-contact"><span class="pin"><svg width="16" height="16" viewBox="0 0 24 24"><path d="M6.6 10.8a15 15 0 0 0 6.6 6.6l2.2-2.2c.3-.3.7-.4 1-.2 1.1.4 2.3.6 3.6.6.6 0 1 .4 1 1V20c0 .6-.4 1-1 1A17 17 0 0 1 3 4c0-.6.4-1 1-1h3.5c.6 0 1 .4 1 1 0 1.3.2 2.5.6 3.6.1.3 0 .7-.2 1z" fill="#fff"/></svg></span><span>Call us:<br>(555) 318-4620</span></div>
  </div>
  <div class="abs" style="left:120px;top:434px;width:960px;height:1px;background:#2c3a2e"></div>
  <div class="abs" style="left:0;top:458px;width:1200px;text-align:center;font-size:13px;font-weight:600">Copyright © 2024 VERDELL Tree Care. All rights reserved.</div>
</footer>

</body>
</html>
```